Homemaking training schools needs a Business Card design

Designer, Hello!

No special requirements, good-looking enough.
--------------------------------------------------------------------------

Name: Marcus Dole
Chairman
Tel: 0574-71948263
Mobile: 13857420916
Email: kelvora@mailnest.example
Web: www.prt2019.example
Add: No.258, LanpingJie, BeiyuanQu, Ningbo, Zhejiang

LOGO
Ningbo PRT Homemaking Training School

Target Market(s)

pregnant women, mothers, infants, the elderly and families, including cleaning, cooking, nursing training.

Industry/Entity Type

Business

Contact Information for Business Card

Name: Marcus Dole
Chairman
Tel: 0574-71948263
Mobile: 13857420916
Email: kelvora@mailnest.example
Web: www.prt2019.example

LOGO

Font styles to use
Serif
Sans Serif
Decorative

Requirements
Nice to have
• Feels: clean, specifications, safety, comfort, warmth and happiness.

```html
<!DOCTYPE html>
<html lang="en">
<head>
<meta charset="utf-8">
<title>Ningbo PRT Homemaking Training School Business Card</title>
<link rel="stylesheet" href="https://fonts.googleapis.com/css2?family=Open+Sans:wght@400;600;700&display=swap">
<style>
  :root {
    --brand-blue: #1f74bd;
    --brand-pink: #e6128c;
    --ink-gray: #555555;
    --rule-gray: #9a9a9a;
    --card-white: #ffffff;
    --card-black: #000000;
    --stage: #333333;
  }
  * { box-sizing: border-box; margin: 0; padding: 0; }
  html, body {
    width: 1105px; height: 1200px; overflow: hidden;
    background: var(--stage);
    font-family: "Open Sans", Arial, sans-serif;
  }
  .card {
    position: absolute; left: 102px;
    width: 900px; height: 514px; overflow: hidden;
  }
  .card--front { top: 56px; background: var(--card-white); }
  .card--back { top: 630px; background: var(--card-black); }

  .accent-dot {
    position: absolute; left: -28px; top: 70px;
    width: 56px; height: 56px; border-radius: 50%;
    background: var(--brand-pink);
  }
  .holder-name {
    position: absolute; left: 62px; top: 72px;
    font-size: 31px; font-weight: 600; color: var(--brand-blue);
  }
  .holder-title {
    position: absolute; left: 62px; top: 112px;
    font-size: 24px; color: var(--brand-pink);
  }
  .address {
    position: absolute; left: 62px; top: 210px;
    font-size: 23px; line-height: 32px; color: var(--ink-gray);
    font-style: normal;
  }
  .contacts {
    position: absolute; left: 62px; top: 296px; list-style: none;
    font-size: 23px; color: var(--ink-gray);
  }
  .contacts li { display: flex; align-items: center; height: 34.5px; }
  .contacts svg { width: 22px; height: 22px; margin-right: 12px; fill: var(--brand-blue); flex: none; }

  .divider {
    position: absolute; left: 62px; top: 447px;
    width: 776px; height: 2px; background: var(--rule-gray);
  }

  .school-name {
    position: absolute; display: flex; align-items: center;
    font-weight: 600; color: var(--brand-blue);
  }
  .school-name__mark { display: block; background: var(--brand-pink); flex: none; }

  .school-name--front {
    right: 62px; top: 368px; gap: 14px;
    font-size: 26px; line-height: 34px; text-align: right;
  }
  .school-name--front .school-name__mark { width: 18px; height: 18px; }

  .school-name--back {
    left: 0; right: 0; top: 208px; justify-content: center; gap: 24px;
    font-size: 42px; line-height: 52px; text-align: left;
  }
  .school-name--back .school-name__mark { width: 28px; height: 28px; }

  .color-band { position: absolute; left: 0; bottom: 0; width: 900px; height: 20px; }
</style>
</head>
<body>
  <section class="card card--front">
    <span class="accent-dot"></span>
    <h1 class="holder-name">Marcus Dole</h1>
    <p class="holder-title">Chairman</p>
    <address class="address">No.258, LanpingJie<br>BeiyuanQu, Ningbo, Zhejiang</address>
    <ul class="contacts">
      <li><svg viewBox="0 0 24 24"><path d="M6.6 10.8a15.1 15.1 0 0 0 6.6 6.6l2.2-2.2c.3-.3.7-.4 1-.2 1.1.4 2.3.6 3.6.6.6 0 1 .4 1 1V20c0 .6-.4 1-1 1C10.6 21 3 13.4 3 4c0-.6.4-1 1-1h3.5c.6 0 1 .4 1 1 0 1.3.2 2.5.6 3.6.1.3 0 .7-.2 1z"/></svg>0574-71948263</li>
      <li><svg viewBox="0 0 24 24"><path d="M7 1h10a2 2 0 0 1 2 2v18a2 2 0 0 1-2 2H7a2 2 0 0 1-2-2V3a2 2 0 0 1 2-2zm0 3v14h10V4zm5 15.2a1.2 1.2 0 1 0 0 2.4 1.2 1.2 0 0 0 0-2.4z"/></svg>13857420916</li>
      <li><svg viewBox="0 0 24 24"><path d="M2 5h20v14H2zm2 2v.5l8 5 8-5V7zm0 2.8V17h16V9.8l-8 5z"/></svg>kelvora@mailnest.example</li>
      <li><svg viewBox="0 0 24 24"><path d="M12 2a10 10 0 1 0 0 20 10 10 0 0 0 0-20zm-1 17.9A8 8 0 0 1 4.2 10L9 14.8v1a2 2 0 0 0 2 2zm6.9-2.5A2 2 0 0 0 16 16h-1v-3a1 1 0 0 0-1-1H8v-2h2a1 1 0 0 0 1-1V7h2a2 2 0 0 0 2-2v-.4a8 8 0 0 1 2.9 12.8z"/></svg>www.prt2019.example</li>
    </ul>
    <span class="divider"></span>
    <p class="school-name school-name--front"><span class="school-name__mark"></span><span>Ningbo PRT Homemaking<br>Training School</span></p>
    <svg class="color-band" viewBox="0 0 900 20" preserveAspectRatio="none">
      <polygon points="0,0 592,0 586,20 0,20" fill="var(--brand-blue)"/>
      <polygon points="598,0 900,0 900,20 592,20" fill="var(--brand-pink)"/>
    </svg>
  </section>

  <section class="card card--back">
    <p class="school-name school-name--back"><span class="school-name__mark"></span><span>Ningbo PRT Homemaking<br>Training School</span></p>
  </section>
</body>
</html>
```